Harrow Point Metrics Company Website Design and Coding

We want to redesign our existing website so that it is more visually and functionally appealing to prospective clients and potential job candidates. We would like to keep our current color scheme and implement our current logo as well. We have a high-level idea of website structure that we are thinking of, which is in the attached files. Logo is included as well. The final design would ideally be energy and analytics focused. We will need the new website to be coded as well, please.

Target Market(s)

Energy and utility industry

Industry/Entity Type

Energy/analytics

Coding

Coded - Design and coding required

Number of Pages Required

5+ page

Font styles to use
Sans Serif

Colors
0094D4
00A9DD
6FCCEA
C7EBF8
E9F6FB
F0912C
F2A743
F7CA91
FBE8D2
FDF5EE

Requirements
Must have
• Consistent color scheme- please use the one that we provided. We need an overview, a home page, and our core services. A separate job application page. Logo must be incorporated. We would like e "Meet our Team" page. Please include all of the content that is listed in our attachments.
Nice to have
• Movement
Should not have
• No music, no cartoons/animation, no pictures of a chalkboard

```html
<!DOCTYPE html>
<html lang="en">
<head>
<meta charset="utf-8">
<title>Harrow Point Metrics</title>
<link href="https://fonts.googleapis.com/css2?family=Barlow:wght@400;500;600;700&family=Roboto:wght@400;500&display=swap" rel="stylesheet">
<style>
:root{
  --orange:#ee6712;
  --orange-soft:#f0912c;
  --blue:#1b5fb5;
  --blue-deep:#1456a8;
  --navy:#071a40;
  --ink:#1b1b1b;
  --text:#3a3a3a;
  --grey-bg:#f1f2f4;
  --white:#ffffff;
  --footer:#07080c;
}
*{box-sizing:border-box;margin:0;padding:0}
html,body{width:1200px;height:4458px;overflow:hidden}
body{font-family:"Roboto",sans-serif;color:var(--text);background:var(--white);position:relative}
h1,h2,h3,h4,.btn,.brand{font-family:"Barlow",sans-serif}
a{color:inherit;text-decoration:none}
.section{position:absolute;left:0;width:1200px}
.btn{display:inline-flex;align-items:center;justify-content:center;border-radius:30px;font-weight:600;font-size:15px;color:var(--white)}
.btn-blue{background:var(--blue)}
.btn-orange{background:var(--orange)}

/* header */
.header{top:0;height:121px;background:var(--white)}
.top-links{position:absolute;top:9px;left:124px;display:flex;gap:30px;font-size:13px;color:#333}
.brand{position:absolute;left:112px;top:44px;display:flex;align-items:center;gap:12px;font-size:28px;font-weight:500;color:var(--blue)}
.brand-dot{width:42px;height:42px;border-radius:50%;background:var(--blue)}
.main-nav{position:absolute;right:0;top:69px;width:698px;height:52px;background:var(--orange);clip-path:polygon(22px 0,100% 0,100% 100%,0 100%)}
.main-nav ul{list-style:none;display:flex;gap:42px;position:absolute;left:76px;top:16px;font-size:15px;color:var(--white)}

/* hero */
.hero{top:121px;height:740px;overflow:hidden}
.hero-art{position:absolute;inset:0;background:radial-gradient(ellipse at 78% 40%,#1f4fa8 0%,#0d2c6e 35%,#071a40 75%)}
.hero-text{position:absolute;left:111px;top:168px;width:560px;color:var(--white)}
.hero-text .kicker{font-size:50px;font-weight:700;color:var(--orange);line-height:1}
.hero-text h1{font-size:50px;font-weight:700;line-height:1.25}
.hero-text p{font-size:15px;line-height:26px;margin-top:14px}
.hero-text .btn{margin-top:30px;width:164px;height:55px;background:#1a6ad1}
.hero-wave{position:absolute;left:0;bottom:0;width:1200px;height:160px}

/* services */
.services{top:861px;height:767px}
.section-title{font-size:34px;font-weight:600;color:var(--ink);text-align:center}
.services .section-title{margin-top:52px}
.cards{position:absolute;top:129px;left:113px;display:flex;gap:18px}
.card{width:313px;height:465px;border:2px solid var(--orange);padding:42px 22px 0 22px;background:var(--white)}
.card svg{width:110px;height:110px}
.card h3{font-size:21px;font-weight:600;color:var(--ink);margin-top:24px;line-height:26px}
.card ul{list-style:none;margin-top:16px;font-size:14px;line-height:26px;color:#333}
.card .more{display:inline-block;margin-top:8px;margin-left:4px;font-size:14px;color:var(--orange);text-decoration:underline}
.card-feature{border:none;background:linear-gradient(180deg,#ef7a2a 0%,#d98a4e 45%,#3f86c9 80%,#2a7ad0 100%);color:var(--white)}
.card-feature h3,.card-feature ul,.card-feature .more{color:var(--white)}
.services .btn{position:absolute;left:530px;top:639px;width:142px;height:55px}

/* research */
.research{top:1628px;height:561px;background:var(--grey-bg)}
.research-photo{position:absolute;left:113px;top:74px;width:415px;height:415px;border-radius:50%;background:linear-gradient(135deg,#d8cbb6,#efe9df 45%,#b9a58c);box-shadow:10px 0 0 var(--orange)}
.research-copy{position:absolute;left:573px;top:127px;width:480px}
.research-copy h2{font-size:34px;font-weight:600;color:var(--ink)}
.research-copy h4{font-size:19px;font-weight:600;color:var(--blue);margin-top:14px}
.research-copy p{font-size:14px;line-height:25px;color:#333;margin-top:6px}
.research-copy .btn{margin-top:30px;width:168px;height:57px}

/* overview */
.overview{top:2189px;height:395px}
.overview .section-title{margin-top:68px}
.overview p{width:900px;margin:24px auto 0;text-align:center;font-size:14.5px;line-height:26px;color:#333}
.overview .btn{position:absolute;left:524px;top:259px;width:154px;height:57px}

/* cases */
.cases{top:2584px;height:626px;background:linear-gradient(160deg,#1a67bf,#1456a8 55%,#1d6cc8)}
.cases .section-title{color:var(--white);margin-top:70px}
.case-list{position:absolute;top:164px;left:95px;display:flex;gap:12px}
.case{width:242px;text-align:center;color:var(--white)}
.case-photo{width:203px;height:203px;border-radius:50%;margin:0 auto}
.case h4{font-size:21px;font-weight:600;line-height:26px;margin-top:20px}
.cases .btn{position:absolute;left:524px;top:486px;width:154px;height:57px}

/* team */
.team{top:3210px;height:594px}
.team-copy{position:absolute;left:111px;top:132px;width:510px}
.team-copy h2{font-size:34px;font-weight:600;color:var(--ink)}
.team-copy p{font-size:14.5px;line-height:26px;color:#333;margin-top:16px}
.team-copy .btn{margin-top:32px;width:168px;height:57px}
.team-photo{position:absolute;left:661px;top:80px;width:416px;height:416px;border-radius:50%;background:linear-gradient(135deg,#1f3c6a,#4f6f99 50%,#b8c3d2);box-shadow:-10px -6px 0 var(--orange)}

/* careers */
.careers{top:3784px;height:320px;background:linear-gradient(90deg,#e8600e,#f07a22 60%,#e66512)}
.careers h2{position:absolute;left:111px;top:34px;font-size:34px;font-weight:600;color:var(--white)}
.careers p{position:absolute;left:111px;top:84px;width:790px;font-size:14px;line-height:26px;color:var(--white)}
.careers .btn{position:absolute;left:920px;top:132px;width:168px;height:57px}

/* footer */
.footer{top:4040px;height:418px}
.footer-curve{position:absolute;left:0;top:0;width:1200px;height:418px}
.footer-brand{position:absolute;left:108px;top:96px;display:flex;align-items:center;gap:10px;font-family:"Barlow",sans-serif;font-size:23px;font-weight:500;color:#3b8fe0}
.footer-brand span.dot{width:32px;height:32px;border-radius:50%;background:#3b8fe0}
.socials{position:absolute;left:185px;top:160px;display:flex;gap:10px}
.socials span{width:27px;height:27px;border-radius:50%;background:#e6e6e6}
.socials span:first-child{background:var(--orange)}
.footer-col{position:absolute;top:78px;color:var(--white)}
.footer-col h4{font-size:21px;font-weight:600;margin-bottom:16px}
.footer-col ul{list-style:none;font-size:14px;line-height:30px}
.footer-col li::before{content:"«";margin-right:8px}
.col-quick{left:443px}
.col-help{left:620px}
.col-news{left:812px}
.col-news input{display:block;width:278px;height:40px;border:1px solid #555;border-radius:4px;background:transparent;padding:0 16px;font-size:14px;color:#999;font-family:"Roboto",sans-serif}
.col-news .btn{margin-top:12px;width:278px;height:40px;border-radius:4px;background:var(--blue)}
.copyright{position:absolute;left:0;width:1200px;top:360px;text-align:center;font-size:14px;color:var(--white)}
</style>
</head>
<body>

<header class="section header">
  <nav class="top-links">
    <a href="#">Forecating &amp; Perdictive Analytics</a>
    <a href="#">T&amp;D Planning</a>
    <a href="#">Evaluation</a>
    <a href="#">Pilot&amp; Emerging Tech Support</a>
    <a href="#">Program &amp; Portfolio Resource Planning</a>
    <a href="#">more</a>
  </nav>
  <a class="brand" href="#"><span class="brand-dot"></span>Harrow Point Metrics</a>
  <nav class="main-nav">
    <ul>
      <li>Core Services</li><li>About</li><li>Our Work</li><li>Blog</li><li>Contatc Us</li>
    </ul>
  </nav>
</header>

<section class="section hero">
  <div class="hero-art" role="img" aria-label="Dark blue financial data visualisation with glowing bar charts and orange line graph"></div>
  <div class="hero-text">
    <div class="kicker">WELCOME TO</div>
    <h1>HARROW POINT METRICS</h1>
    <p>Harrow Point Metrics was formed in 2016 to help utilities and regulatory agencies navigate the technical, economic, and policy challenges of building a smarter and cleaner energy future.</p>
    <a class="btn" href="#">GET STARTED</a>
  </div>
  <svg class="hero-wave" viewBox="0 0 1200 160" preserveAspectRatio="none">
    <path d="M0 90 Q600 190 1200 30 L1200 160 L0 160 Z" fill="#ee6712"/>
    <path d="M0 112 Q600 200 1200 48 L1200 160 L0 160 Z" fill="#ffffff"/>
  </svg>
</section>

<section class="section services">
  <h2 class="section-title">OUR SERVICES</h2>
  <div class="cards">
    <article class="card">
      <svg viewBox="0 0 110 110" fill="none" stroke="#1b5fb5" stroke-width="4">
        <circle cx="64" cy="44" r="30"/><circle cx="64" cy="44" r="22"/>
        <line x1="42" y1="66" x2="16" y2="92" stroke-width="8"/>
        <rect x="52" y="40" width="6" height="16"/><rect x="62" y="30" width="6" height="26"/><rect x="72" y="22" width="6" height="34"/>
      </svg>
      <h3>Predictive Analytics<br>and Forecasting</h3>
      <ul><li>Distributed energy resource integra-tion into planning and operations Granular analysis (8760) and fore-casting of distributed energy resource adoption and impacts on the grid, in-cluding solar, battery storage...</li></ul>
      <a class="more" href="#">Learn More</a>
    </article>
    <article class="card card-feature">
      <svg viewBox="0 0 110 110" fill="none" stroke="#ffffff" stroke-width="4">
        <rect x="8" y="10" width="78" height="64" rx="6"/><line x1="8" y1="24" x2="86" y2="24"/>
        <circle cx="66" cy="70" r="22"/><line x1="82" y1="86" x2="100" y2="104" stroke-width="7"/>
        <line x1="58" y1="78" x2="58" y2="66"/><line x1="66" y1="78" x2="66" y2="58"/><line x1="74" y1="78" x2="74" y2="64"/>
      </svg>
      <h3>T&amp;D Plannin</h3>
      <ul><li>Location specific, probabilistic fore-casting for system, transmission and distribution planning (electric and gas) Non-wire alternative and non-pipe alternative project assess-ments and optimization Expert testi-mony</li></ul>
      <a class="more" href="#">Learn More</a>
    </article>
    <article class="card">
      <svg viewBox="0 0 110 110" fill="none" stroke="#1b5fb5" stroke-width="4">
        <rect x="14" y="8" width="66" height="94" rx="4"/>
        <rect x="24" y="22" width="14" height="14"/><rect x="24" y="46" width="14" height="14"/><rect x="24" y="70" width="14" height="14"/>
        <line x1="46" y1="29" x2="70" y2="29"/><line x1="46" y1="53" x2="70" y2="53"/><line x1="46" y1="77" x2="62" y2="77"/>
        <line x1="96" y1="52" x2="70" y2="96" stroke-width="6"/>
      </svg>
      <h3>Evaluation</h3>
      <ul>
        <li>Demand Response evaluations</li><li>Behavioral program evaluations</li><li>Energy Efficiency evaluations</li>
        <li>Time-varying rate evaluations</li><li>Process and outcome evaluations</li><li>Pilot research design and evaluation</li>
        <li>Ability to provide real-time evaluatio</li>
      </ul>
      <a class="more" href="#">Learn More</a>
    </article>
  </div>
  <a class="btn btn-orange" href="#">View All</a>
</section>

<section class="section research">
  <div class="research-photo" role="img" aria-label="Hands pointing at charts on a tablet during a meeting"></div>
  <div class="research-copy">
    <h2>RESEARCH AND ANALYSIS</h2>
    <h4>Journal Articles and Conference Presentations</h4>
    <p>Links to relevant published journal articles and conference presentations</p>
    <h4>Published Reports</h4>
    <p>Links to published reports</p>
    <a class="btn btn-blue" href="#">Learn More</a>
  </div>
</section>

<section class="section overview">
  <h2 class="section-title">COMPANY OVERVIEW</h2>
  <p>Harrow Point Metrics (HPM) was formed in 2016 to help utilities and regulatory agencies navigate the technical, economic, and policy challenges of building a smarter and cleaner energy future. Our research focuses on impact analysis as well as predictive and causal analytics. We deliver data-driven insights into how various technologies and interventions affect the way homes and businesses use energy and how those in turn affect grid and system planning.</p>
  <a class="btn btn-blue" href="#">Learn More</a>
</section>

<section class="section cases">
  <h2 class="section-title">PROPOSED CASE STUDIES FOR EACH CORE SERVICE</h2>
  <div class="case-list">
    <div class="case"><div class="case-photo" role="img" aria-label="Desk with printed charts and laptop" style="background:linear-gradient(135deg,#c9a887,#efe3d4)"></div><h4>Predictive Analytics and Forecasting</h4></div>
    <div class="case"><div class="case-photo" role="img" aria-label="Team planning with sticky notes on glass wall" style="background:linear-gradient(135deg,#8a8f86,#d9c9a8)"></div><h4>T&amp;D Planning</h4></div>
    <div class="case"><div class="case-photo" role="img" aria-label="Analyst working in front of data screens" style="background:linear-gradient(135deg,#0f2c3a,#2f6a74)"></div><h4>Evaluation</h4></div>
    <div class="case"><div class="case-photo" role="img" aria-label="Person reviewing charts on a computer monitor" style="background:linear-gradient(135deg,#e4e1dc,#9fb7d8)"></div><h4>Pilot &amp; Emerging Tech Support</h4></div>
  </div>
  <a class="btn btn-orange" href="#">Learn More</a>
</section>

<section class="section team">
  <div class="team-copy">
    <h2>OUR TEAM</h2>
    <p>We attract, motivate, and develop highly dedicated team members. All our staff is trained on research methods and analysis of AMI, end-use, and SCADA data specifically related to the electric and gas sectors. Our staff is mainly comprised of data scientist, statisticians, economists, and public policy experts. Most staff is in Atlanta, with additional staff in California, Colorado, and New York.</p>
    <a class="btn btn-blue" href="#">Learn More</a>
  </div>
  <div class="team-photo" role="img" aria-label="Presenter explaining a dashboard on a wall screen to colleagues"></div>
</section>

<section class="section careers">
  <h2>CAREERS</h2>
  <p>At HPM, we are driven to help create a smarter and cleaner energy future, and we are always looking for talented professionals who share our passion for achieving this goal. We are a transparent organization where you will have the opportunity to work directly with our senior energy experts. Our employees get to work on a wide variety of projects and develop new skills so that they are well equipped to interact with our clients find effective ways to solve our clients' problems.</p>
  <a class="btn btn-blue" href="#">Learn More</a>
</section>

<footer class="section footer">
  <svg class="footer-curve" viewBox="0 0 1200 418" preserveAspectRatio="none">
    <path d="M0 60 Q300 10 620 30 Q950 50 1200 5 L1200 418 L0 418 Z" fill="#07080c"/>
  </svg>
  <div class="footer-brand"><span class="dot"></span>Harrow Point Metrics</div>
  <div class="socials"><span></span><span></span><span></span><span></span></div>
  <div class="footer-col col-quick">
    <h4>QUICK LINKS</h4>
    <ul><li>Core Services</li><li>About</li><li>Our Work</li><li>Blog</li><li>Contatc Us</li></ul>
  </div>
  <div class="footer-col col-help">
    <h4>HELP LINKS</h4>
    <ul><li>Terms&amp;conditions</li><li>Privacy Policy</li><li>About Us</li><li>Support</li></ul>
  </div>
  <div class="footer-col col-news">
    <h4>GET OUR NEWSLETTER</h4>
    <input type="email" placeholder="Enter Your Email">
    <a class="btn" href="#">SUBSCRIBE NOW</a>
  </div>
  <div class="copyright">©Copyrights 2022 Harrow Point Metrics | &nbsp;All Rights Reserved</div>
</footer>

</body>
</html>
```